Charity Initiative needs a WebPage design

We need a web design for charity initiative by two young guys riding their bikes around Australia to support HarbourLight which helps people with depression and anxiety. Full brief and requirements are attached in the PDF and word document. We have the logo already done and attached. Website will be done in Wordpress and need to get Donations, display current donations, show live Video feed, GPS tracker, Blogs etc and also ability to sell merchandise later

Target Market(s)

Sponsors, Business, Young People

Number of Pages Required

4 page

Font styles to use
Serif
Sans Serif
Decorative
Script

Requirements
Must have
• As per Brief and also Donation status etc
Nice to have
• Please check my logo and read the Bried

```html
<!DOCTYPE html>
<html lang="en">
<head>
<meta charset="utf-8">
<title>Road to the Rim — Charity Ride</title>
<link href="https://fonts.googleapis.com/css2?family=Oswald:wght@400;500&family=Roboto:wght@400;500&display=swap" rel="stylesheet">
<style>
:root{
  --teal:#3dbcb0;
  --teal-dark:#2a9a90;
  --pink:#e2185a;
  --pink-dark:#c3124c;
  --ink:#222;
  --muted:#666;
  --dark:#131718;
  --darker:#0b0e0f;
  --white:#fff;
}
*{box-sizing:border-box;margin:0;padding:0}
html,body{width:1200px;height:2639px;overflow:hidden}
body{font-family:"Roboto",Arial,sans-serif;color:var(--ink);background:var(--white);position:relative}
.abs{position:absolute}
.head-font{font-family:"Oswald","Arial Narrow",sans-serif;font-weight:400;text-transform:uppercase}
.accent-pink{color:var(--pink)}
.accent-teal{color:var(--teal)}

/* Header */
.site-header{position:absolute;left:0;top:0;width:1200px;height:127px;background:var(--white)}
.brand{position:absolute;left:115px;top:30px;display:flex;align-items:center;gap:10px;font-family:"Oswald",sans-serif;font-weight:500;font-size:30px;color:var(--pink);text-transform:uppercase}
.brand-dot{width:30px;height:30px;border-radius:50%;background:var(--pink)}
.social{position:absolute;top:18px;left:987px;display:flex;gap:10px}
.social span{width:27px;height:27px;border-radius:50%;border:1px solid #cfd6d6;background:#f3f6f6}
.nav-bar{position:absolute;left:352px;top:68px;width:848px;height:59px}
.nav{position:absolute;left:395px;top:76px;display:flex;align-items:center;height:42px;font-size:12px;font-weight:500;color:var(--white);text-transform:uppercase}
.nav a{color:var(--white);text-decoration:none;padding:0 25px;line-height:34px}
.nav a.active{background:var(--teal-dark);padding:0 20px}
.nav a.donate{background:var(--pink);line-height:42px;width:178px;text-align:center;margin-left:33px;padding:0}

/* Hero */
.hero{position:absolute;left:0;top:127px;width:1200px;height:506px;background:linear-gradient(160deg,#3f4146 0%,#8a7560 35%,#d9a865 52%,#9d7c5b 66%,#3b3633 100%)}
.hero h1{position:absolute;left:112px;top:180px;font-size:45px;color:var(--white);letter-spacing:.5px;font-family:"Oswald",sans-serif;font-weight:400}
.hero p{position:absolute;left:112px;top:248px;width:620px;font-size:15px;line-height:27px;color:var(--white)}
.btn-hero{position:absolute;left:112px;top:325px;width:263px;height:63px;background:var(--pink);color:var(--white);font-family:"Oswald",sans-serif;font-size:17px;text-transform:uppercase;display:flex;align-items:center;justify-content:center;gap:10px;box-shadow:0 3px 0 var(--pink-dark)}
.dots{position:absolute;left:558px;top:468px;display:flex;gap:12px}
.dots span{width:11px;height:11px;border-radius:50%;background:#ddd}
.dots span.on{background:var(--pink);box-shadow:0 0 0 2px #fff}

/* Sections */
.section-title{position:absolute;left:0;width:1200px;text-align:center;font-size:28px;font-family:"Oswald",sans-serif;text-transform:uppercase;letter-spacing:-.3px}
.welcome-text{position:absolute;left:110px;top:728px;width:980px;text-align:center;font-size:12px;line-height:33px;color:var(--muted)}
.divider{position:absolute;left:110px;top:848px;width:980px;height:8px;border-radius:50%;box-shadow:0 6px 8px -4px rgba(0,0,0,.35)}

.card{position:absolute;top:968px;width:296px;height:204px;box-shadow:0 6px 12px rgba(0,0,0,.2);overflow:hidden}
.card-photo{position:absolute;left:0;top:0;width:100%}
.card-caption{position:absolute;left:0;bottom:0;width:100%;height:58px;background:var(--teal);color:var(--white);font-size:15px;text-transform:uppercase;display:flex;align-items:center;justify-content:center}
.card-open{position:absolute;left:0;top:78px;width:100%;height:126px;background:var(--teal);color:var(--white);text-align:center}
.card-open .amount{margin-top:38px;font-size:19px}
.card-open .blurb{margin:6px 22px 0;font-size:11px;line-height:20px}
.plus{position:absolute;left:115px;top:45px;width:66px;height:66px;border-radius:50%;background:var(--pink)}

.target{position:absolute;left:0;top:1232px;width:1200px;height:232px;background:var(--pink);color:var(--white)}
.target .section-title{top:44px;color:var(--white)}
.stat{position:absolute;font-size:19px}
.stat small{display:block;font-size:10px;margin-top:2px}
.bar{position:absolute;left:250px;top:135px;width:670px;height:13px;border-radius:7px;background:#1a1a1a}
.bar-fill{position:absolute;left:0;top:0;width:402px;height:13px;border-radius:7px;background:var(--teal)}
.bar-tag{position:absolute;left:388px;top:-22px;background:#2b6e69;color:#fff;font-size:9px;padding:2px 5px}

.videos{position:absolute;left:0;top:1464px;width:1200px;height:494px;background:radial-gradient(ellipse at 80% 30%,#3a3c3e 0%,#1c1e1f 55%,#111 100%)}
.videos .section-title{top:50px;color:var(--white)}
.video-card{position:absolute;top:132px;width:450px;height:312px;background:var(--white)}
.video-card h3{margin-top:34px;text-align:center;font-size:14px;font-weight:400;color:#333;text-transform:uppercase}
.video-frame{position:absolute;left:30px;top:76px;width:390px;height:194px}
.play{position:absolute;left:170px;top:72px}

.track{position:absolute;left:0;top:1958px;width:1200px;height:387px}
.map{position:absolute;left:0;top:0;width:515px;height:387px;background:linear-gradient(135deg,#a9c7ea 0%,#d7e2c7 40%,#e9e3cf 60%,#aac6ea 100%)}
.track-tab{position:absolute;left:515px;top:0;width:70px;height:387px;background:var(--pink)}
.track-tab span{position:absolute;left:35px;top:193px;transform:translate(-50%,-50%) rotate(-90deg);white-space:nowrap;font-family:"Oswald",sans-serif;font-size:24px;color:#fff;text-transform:uppercase}
.journal-title{position:absolute;left:610px;top:30px;font-size:27px;font-family:"Oswald",sans-serif;text-transform:uppercase}
.entry{position:absolute;left:612px;width:480px;height:104px}
.entry-thumb{position:absolute;left:0;top:0;width:150px;height:104px;box-shadow:0 4px 8px rgba(0,0,0,.25)}
.entry-date{position:absolute;left:0;bottom:0;width:150px;height:30px;background:var(--teal);color:#fff;font-size:11px;display:flex;align-items:center;justify-content:center}
.entry-text{position:absolute;left:178px;top:-6px;width:300px;font-size:12px;line-height:25px;color:#222}
.entry-text em{display:block;font-style:normal;color:var(--muted);font-size:11px}

.footer{position:absolute;left:0;top:2345px;width:1200px;height:215px;background:var(--dark);color:#e6e6e6;font-size:11px}
.footer h4{font-family:"Oswald",sans-serif;font-weight:400;font-size:15px;text-transform:uppercase;margin-bottom:18px;color:#fff}
.fcol{position:absolute;top:35px}
.fbrand{display:flex;align-items:center;gap:8px;font-family:"Oswald",sans-serif;font-size:17px;color:#fff;margin-bottom:14px}
.fbrand i{width:18px;height:18px;border-radius:50%;background:var(--teal)}
.fcol p,.fcol li{line-height:24px;list-style:none}
.fcol li::before{content:"";display:inline-block;border-left:5px solid #fff;border-top:4px solid transparent;border-bottom:4px solid transparent;margin-right:6px}
.news{display:flex;margin-top:16px}
.news span{width:144px;height:30px;background:#eee;color:#777;font-size:10px;padding:9px 10px}
.news b{width:56px;height:30px;background:var(--pink);color:#fff;font-size:11px;font-weight:500;display:flex;align-items:center;justify-content:center}
.copy{position:absolute;left:0;top:2560px;width:1200px;height:79px;background:var(--darker);color:#ddd;font-size:11px;text-align:center;line-height:79px}
</style>
</head>
<body>

<header class="site-header">
  <div class="brand"><span class="brand-dot"></span>Road to the Rim</div>
  <div class="social"><span></span><span></span><span></span></div>
  <svg class="nav-bar" viewBox="0 0 848 59" width="848" height="59"><polygon points="30,0 848,0 848,59 0,59" fill="#3dbcb0"/></svg>
  <nav class="nav">
    <a class="active">Home</a><a>Journal</a><a>Riders</a><a>Supporters</a><a>Contact</a><a class="donate">Make a Donation</a>
  </nav>
</header>

<section class="hero" role="img" aria-label="Rider on a motorbike heading down an open highway at sunset">
  <h1>TWO MATES. TWO BIKES. ONE LONG ROAD.</h1>
  <p>Lorem ipsum dolor sit amet, consectetur adipiscing elit. Nulla rhoncus semper eros, vitae semper, magna mollis vel.</p>
  <div class="btn-hero">
    <svg width="14" height="14" viewBox="0 0 14 14"><circle cx="7" cy="7" r="7" fill="#fff"/><path d="M5 4l4 3-4 3z" fill="#e2185a"/></svg>
    Get Donations
  </div>
  <div class="dots"><span></span><span></span><span class="on"></span><span></span></div>
</section>

<h2 class="section-title" style="top:680px">Welcome to <span class="accent-pink">Road to the Rim</span></h2>
<p class="welcome-text">Aliquam sit amet sagittis justo. Nunc vitae velit sed mauris pulvinar eleifend pulvinar vel justo. Etiam nulla odio, lacinia non blandit at, aliquam vitae sapien. Donec sit amet cursus leo. Morbi imperdiet, mauris et efficitur placerat, odio arcu faucibus erat, sit amet placerat ligula erat vel tortor. Nulla consectetur dictum mi id bibendum. Cras viverra vitae diam ut sodales. Suspendisse bibendum ac nunc quis ornare. Nunc libero lacus, egestas nec molestie ac, molestie quis lorem.</p>
<div class="divider"></div>

<h2 class="section-title" style="top:898px">Current <span class="accent-pink">Donations</span></h2>

<div class="card" style="left:110px">
  <div class="card-photo" style="height:78px;background:linear-gradient(180deg,#b9c8b0,#6f7f5c)" role="img" aria-label="Motorbike mirror beside a tree-lined road"></div>
  <div class="card-open">
    <div class="amount">$ 250.00</div>
    <div class="blurb">Lorem ipsum dolor sit amet, consectetur adipiscing elit. Maecenas ullamcorper.</div>
  </div>
  <div class="plus"><svg width="66" height="66" viewBox="0 0 66 66"><rect x="30" y="21" width="6" height="24" fill="#fff"/><rect x="21" y="30" width="24" height="6" fill="#fff"/></svg></div>
</div>
<div class="card" style="left:450px">
  <div class="card-photo" style="height:146px;background:linear-gradient(180deg,#e6b36a,#8b7654 60%,#4c4a40)" role="img" aria-label="Handlebars of a motorbike on a sunlit country road"></div>
  <div class="card-caption">Aenean Commodo Lorem</div>
</div>
<div class="card" style="left:790px">
  <div class="card-photo" style="height:146px;background:linear-gradient(180deg,#dfe6ec,#b5bcc2 60%,#c8a24a)" role="img" aria-label="Helmeted rider seated on a touring motorbike"></div>
  <div class="card-caption">Integer Nec Turpis Ferm</div>
</div>

<section class="target">
  <h2 class="section-title">Donation Target</h2>
  <div class="stat" style="left:167px;top:124px">$ 1,172<small>Raised</small></div>
  <div class="bar"><div class="bar-fill"></div><div class="bar-tag">60%</div></div>
  <div class="stat" style="left:940px;top:124px">$ 2,000<small>Goal</small></div>
  <div class="stat" style="left:0;width:1200px;text-align:center;top:164px">367<small>Donors</small></div>
</section>

<section class="videos">
  <h2 class="section-title">Our <span class="accent-teal">Live Videos</span></h2>
  <div class="video-card" style="left:120px">
    <h3>Nulla rhoncus semper eros, vitae semper magna</h3>
    <div class="video-frame" style="background:linear-gradient(180deg,#b8c3bd,#5e7a4e 55%,#3c4a33)" role="img" aria-label="Rider on a winding mountain road">
      <svg class="play" width="50" height="50" viewBox="0 0 50 50"><circle cx="25" cy="25" r="22" fill="rgba(255,255,255,.15)" stroke="#fff" stroke-width="3"/><path d="M20 15l14 10-14 10z" fill="#fff"/></svg>
    </div>
  </div>
  <div class="video-card" style="left:628px">
    <h3>Integer nec turpis fermentum turpis varius</h3>
    <div class="video-frame" style="background:linear-gradient(180deg,#8fb3d3,#4c7fa9 55%,#b59a74 80%)" role="img" aria-label="Orange motorbike parked by the sea">
      <svg class="play" width="50" height="50" viewBox="0 0 50 50"><circle cx="25" cy="25" r="22" fill="rgba(255,255,255,.15)" stroke="#fff" stroke-width="3"/><path d="M20 15l14 10-14 10z" fill="#fff"/></svg>
    </div>
  </div>
</section>

<section class="track">
  <div class="map" role="img" aria-label="Map of Australia showing the riders' live position"></div>
  <div class="track-tab"><span>Track Our Bikes</span></div>
  <h2 class="journal-title">Recent <span class="accent-pink">Journal</span></h2>
  <article class="entry" style="top:97px">
    <div class="entry-thumb" style="background:linear-gradient(180deg,#2a2012,#b57a2a 55%,#3b2c18)" role="img" aria-label="Highway lights streaking at night"></div>
    <div class="entry-date">Mar 02, 2016</div>
    <div class="entry-text">Lorem ipsum dolor sit amet, consectetur adipiscing elit. Integer enim mauris, iaculis sit amet<em>Duis dapibus nisi eget ultricies posuere. Sed non elit id risus commodo fermentum.</em></div>
  </article>
  <article class="entry" style="top:247px">
    <div class="entry-thumb" style="background:linear-gradient(180deg,#c4ccd2,#7a8a8f 60%,#4a5558)" role="img" aria-label="Two riders side by side on the road"></div>
    <div class="entry-date">Mar 02, 2016</div>
    <div class="entry-text">Duis dapibus nisi eget ultricies posuere. Sed non elit id risus commodo fermentum.<em>Suspendisse viverra laoreet elit, non lacinia eros imperd et a. Nunc aliquam blandit ipsum, a placerat eros.</em></div>
  </article>
</section>

<footer class="footer">
  <div class="fcol" style="left:110px;width:300px">
    <h4>HarbourLight</h4>
    <div class="fbrand"><i></i>HarbourLight</div>
    <p>Aenean commodo lorem dui, quis laoreet dolor blandit ac. Lorem ipsum dolor sit amet, consectetur.</p>
  </div>
  <div class="fcol" style="left:450px">
    <h4>Links</h4>
    <ul><li>Journal</li><li>Riders</li><li>Supporters</li><li>FAQs</li><li>Contact Us</li></ul>
  </div>
  <div class="fcol" style="left:635px;width:200px">
    <h4>Get in Touch</h4>
    <p>Address : 18 Coastline Road, Level</p>
    <p>Lorem Ipsm - 123 456</p>
    <p style="margin-top:2px">Phone : (02) 5550 1482</p>
    <p>Email : info@roadtotherim.org</p>
  </div>
  <div class="fcol" style="left:885px;width:210px">
    <h4>Newsletter</h4>
    <p style="line-height:18px">Your about us information would fit here nicely.</p>
    <div class="news"><span>Email address</span><b>SUBMIT</b></div>
  </div>
</footer>
<div class="copy">Copyright © 2016. All Rights Reserved</div>

</body>
</html>
```